Los Angeles based Demolition, Grading, and Structural concrete Contractor in need of a Sale brochure

We are a Los Angeles-based demolition, grading, and structural concrete contractor looking for a professionally designed sales brochure that represents our company and services. The brochure should be visually appealing, easy to read, and include the following:

-Company Logo: Prominently displayed to enhance brand identity.

-Services We Offer: A clear breakdown of our key services, including demolition, grading, and structural concrete work.

-Project Scope & Capabilities: A brief explanation of the type of projects we handle (residential, commercial, industrial).

-Pricing Information: Mention that demolition services start at $20,000. This price includes complete demolition of structure, safe debris removal and hauling, site preparation for new construction.

-Contact Information: Our phone number(818.502.6617), email(contact@brovanbuildersinc.example) , and website for potential clients to reach out.

The design should reflect the professionalism and strength of our industry, using a modern, clean layout with bold colors that align with construction and demolition themes. Images of past work or stock photos representing our services are encouraged.

Final deliverables should be print-ready (PDF) and digital-friendly formats. Looking forward to creative and impactful designs!

```html
<!DOCTYPE html>
<html lang="en">
<head>
<meta charset="utf-8">
<title>Brovan Builders – Sales Brochure</title>
<link href="https://fonts.googleapis.com/css2?family=Montserrat:wght@500;700;800&family=Open+Sans:wght@400;600;700&family=Oswald:wght@600&display=swap" rel="stylesheet">
<style>
:root{
  --blue:#1b6cb8;
  --blue-deep:#0f5aa3;
  --blue-dark:#0d4f92;
  --ink:#1d1d1f;
  --grey:#8c8e91;
  --grey-light:#b5b7ba;
  --paper:#eff0f2;
  --white:#ffffff;
  --stage:#c4c5c7;
  --photo-sky:#8fb4d8;
  --photo-earth:#b89a70;
}
*{margin:0;padding:0;box-sizing:border-box}
html,body{width:1200px;height:2318px;overflow:hidden}
body{background:var(--stage);position:relative;font-family:"Open Sans",sans-serif;color:var(--ink)}
.page{position:absolute;overflow:hidden;box-shadow:0 6px 18px rgba(0,0,0,.25)}
.page > svg.bg{position:absolute;inset:0}
.layer{position:absolute}

/* brand name */
.brand{font-family:"Montserrat",sans-serif;font-weight:800;color:var(--blue);line-height:1;display:flex;align-items:center;gap:10px}
.brand .mark{width:18px;height:18px;background:var(--blue)}
.brand-sub{font-family:"Montserrat",sans-serif;font-weight:500;letter-spacing:.55em;color:var(--grey-light)}

/* cover */
.cover{left:30px;top:390px;width:560px;height:745px;background:var(--paper)}
.cover .logo{left:22px;top:48px}
.cover .logo .brand{font-size:44px}
.cover .logo .brand-sub{font-size:15px;margin-top:10px}
.cover .welcome{left:0;width:560px;top:485px;text-align:center;font-family:"Montserrat",sans-serif;font-weight:500;font-size:38px;color:#6f7174}
.cover .title{left:0;width:560px;top:530px;text-align:center;font-family:"Oswald",sans-serif;font-weight:600;font-size:62px;line-height:1.2;color:var(--blue);white-space:nowrap}
.url-band{display:flex;align-items:center;gap:6px}
.url-band .slash{width:5px;height:28px;background:var(--grey);transform:skewX(-30deg)}
.url-band .bar{background:var(--blue);color:var(--white);font-family:"Open Sans",sans-serif;font-size:19px;padding:1px 24px;transform:skewX(-30deg)}
.url-band .bar span{display:inline-block;transform:skewX(30deg)}
.cover .url-band{left:0;width:560px;top:660px;justify-content:center}

/* back */
.back{left:610px;top:390px;width:560px;height:745px;background:var(--blue)}
.back .offer{left:0;width:560px;top:118px;text-align:center;color:var(--white);font-family:"Montserrat",sans-serif;font-weight:700}
.offer .line1{font-size:31px}
.offer .line2{display:flex;justify-content:center;align-items:center;gap:12px;font-size:31px;margin-top:6px}
.offer .price{background:var(--white);color:var(--blue-deep);font-weight:800;font-size:36px;padding:0 18px 0 26px;clip-path:polygon(0 0,100% 0,100% 100%,0 100%,10px 50%)}
.offer p{font-family:"Open Sans",sans-serif;font-weight:400;font-size:13.5px;line-height:19px;margin-top:14px}
.back .logo{left:0;width:560px;top:300px;display:flex;flex-direction:column;align-items:center}
.back .logo .brand{font-size:44px;color:var(--blue-deep)}
.back .logo .brand .mark{background:var(--blue-deep)}
.back .logo .brand-sub{font-size:15px;color:#3d8ad4;margin-top:10px}
.back .contact{right:62px;top:488px;text-align:right}
.contact h3{font-family:"Montserrat",sans-serif;font-weight:800;font-size:23px;line-height:26px;color:var(--blue)}
.contact ul{list-style:none;margin-top:10px}
.contact li{display:flex;justify-content:flex-end;align-items:center;gap:10px;font-size:14px;line-height:25px;color:var(--ink)}
.contact li svg{width:13px;height:13px;flex:none}
.contact li + li{border-top:1px solid #d4d6d9}
.back .note{right:62px;top:705px;font-size:8.5px;font-family:"Open Sans",sans-serif;color:var(--ink)}
.back .chat{left:452px;top:440px}

/* spread */
.spread{left:30px;top:1215px;width:1140px;height:700px;box-shadow:0 6px 18px rgba(0,0,0,.25)}
.spread .page{top:0;height:700px;width:570px;box-shadow:none}
.services{left:0;background:linear-gradient(135deg,#1b6cb8,#0e5aa2)}
.about{left:570px;background:var(--paper)}
.section-title{font-family:"Montserrat",sans-serif;font-weight:800;font-size:20px;letter-spacing:.3px}
.section-title::after{content:"";display:block;width:150px;height:2px;margin-top:6px;background:currentColor;opacity:.6}
.services .section-title{color:var(--white);left:38px;top:32px}
.service{position:absolute;left:38px;width:302px;color:var(--white)}
.service h4{font-family:"Montserrat",sans-serif;font-weight:700;font-size:14.5px;display:flex;align-items:center;gap:12px;margin-bottom:6px}
.service h4 svg{width:20px;height:18px}
.service p{font-size:9.2px;line-height:13.6px;text-align:justify;opacity:.95}
.svc-demolition{top:84px}
.svc-grading{top:276px}
.svc-concrete{top:470px}
.photo{position:absolute}
.page-num{position:absolute;font-family:"Montserrat",sans-serif;font-size:10px;font-weight:600}
.services .page-num{left:38px;top:662px;color:var(--white)}
.about .page-num{right:38px;top:662px;color:var(--grey)}
.footer-url{position:absolute;top:655px;height:30px;display:flex;align-items:center;gap:5px}
.footer-url .bar{height:30px;display:flex;align-items:center;font-size:19px;padding:0 22px}
.services .footer-url{right:0}
.services .footer-url .slash{width:4px;height:30px;background:#5d9bd6;transform:skewX(-30deg)}
.services .footer-url .bar{background:#2a7cc8;color:var(--white);clip-path:polygon(14px 0,100% 0,100% 100%,0 100%)}
.about .footer-url{left:0}
.about .footer-url .slash{width:4px;height:30px;background:var(--grey);transform:skewX(30deg)}
.about .footer-url .bar{background:var(--blue);color:var(--white);clip-path:polygon(0 0,100% 0,calc(100% - 14px) 100%,0 100%)}
.about .intro-title{right:38px;top:34px;color:var(--white);font-family:"Montserrat",sans-serif;font-weight:800;font-size:20px}
.about .intro{right:38px;top:74px;width:320px;color:var(--white);font-size:9.4px;line-height:13.8px;text-align:right}
.about .who{left:38px;top:335px;color:var(--blue)}
.about .who-text{left:38px;top:374px;width:300px;font-size:9.2px;line-height:13.6px;text-align:justify}
.who-text p + p{margin-top:13px}
</style>
</head>
<body>

<!-- COVER -->
<section class="page cover">
  <svg class="bg" width="560" height="745" viewBox="0 0 560 745">
    <polygon points="0,0 380,0 0,335" fill="var(--ink)"/>
    <polygon points="380,0 432,0 0,392 0,335" fill="var(--grey)"/>
    <path d="M440 0 H560 V468 H130 Q60 468 40 395 Z" fill="var(--blue)"/>
    <path d="M470 0 H560 V395 Q560 415 540 415 H118 Q95 415 102 395 Z" fill="var(--photo-earth)" role="img" aria-label="Photo: excavator working on a hillside site beside a new retaining wall"/>
    <path d="M470 0 H560 V170 H290 Z" fill="var(--photo-sky)" opacity=".85"/>
  </svg>
  <div class="layer logo">
    <div class="brand"><span class="mark"></span>BROVAN</div>
    <div class="brand-sub">BUILDERS</div>
  </div>
  <div class="layer welcome">Welcome to</div>
  <div class="layer title">BROVAN BUILDERS</div>
  <div class="layer url-band"><span class="slash"></span><span class="slash"></span><span class="bar"><span>www.brovanbuildersinc.example</span></span><span class="slash"></span><span class="slash"></span></div>
</section>

<!-- BACK -->
<section class="page back">
  <svg class="bg" width="560" height="745" viewBox="0 0 560 745">
    <defs><linearGradient id="bk" x1="0" y1="0" x2="1" y2="1"><stop offset="0" stop-color="#1f74c2"/><stop offset="1" stop-color="#0d58a0"/></linearGradient></defs>
    <rect width="560" height="745" fill="url(#bk)"/>
    <polygon points="560,270 560,745 0,745" fill="var(--paper)"/>
    <polygon points="560,290 560,745 522,745 522,323" fill="var(--grey)"/>
  </svg>
  <div class="layer offer">
    <div class="line1">Demolition Services</div>
    <div class="line2"><span>Start at</span><span class="price">$20,000</span></div>
    <p>This price includes complete demolition of structure,<br>safe debris removal and hauling, site preparation<br>for new construction.</p>
  </div>
  <div class="layer logo">
    <div class="brand"><span class="mark"></span>BROVAN</div>
    <div class="brand-sub">BUILDERS</div>
  </div>
  <svg class="layer chat" width="44" height="40" viewBox="0 0 44 40">
    <path d="M14 2 H42 V20 H34 L30 25 V20 H14 Z" fill="#a3a5a8"/>
    <path d="M2 14 H26 V30 H12 L7 36 V30 H2 Z" fill="#8c8e91"/>
    <g fill="#fff"><circle cx="9" cy="22" r="1.6"/><circle cx="14" cy="22" r="1.6"/><circle cx="19" cy="22" r="1.6"/></g>
  </svg>
  <div class="layer contact">
    <h3>Contact<br>Information</h3>
    <ul>
      <li>818.502.6617 <svg viewBox="0 0 14 14"><circle cx="7" cy="7" r="7" fill="var(--blue)"/><path d="M4.5 3.5 L6 5 L5.2 6 Q6 7.8 8 8.8 L9 8 L10.5 9.5 L9.5 10.5 Q5 10 3.5 4.5 Z" fill="#fff"/></svg></li>
      <li>www.brovanbuildersinc.example <svg viewBox="0 0 14 14"><circle cx="7" cy="7" r="7" fill="var(--blue)"/><rect x="3.5" y="4.5" width="7" height="5" rx="1" fill="#fff"/></svg></li>
      <li>contact@brovanbuildersinc.example <svg viewBox="0 0 14 14"><circle cx="7" cy="7" r="7" fill="var(--blue)"/><circle cx="7" cy="7" r="3.6" fill="none" stroke="#fff" stroke-width="1"/><line x1="3.4" y1="7" x2="10.6" y2="7" stroke="#fff" stroke-width="1"/><ellipse cx="7" cy="7" rx="1.5" ry="3.6" fill="none" stroke="#fff" stroke-width="1"/></svg></li>
    </ul>
  </div>
  <div class="layer note">When you are ready to discuss your project, please reach out to us at Brovan Builders.</div>
</section>

<!-- INNER SPREAD -->
<div class="layer spread">
  <section class="page services">
    <h2 class="layer section-title">OUR SERVICES</h2>

    <article class="service svc-demolition">
      <h4><svg viewBox="0 0 20 18"><rect x="1" y="5" width="11" height="12" fill="#fff"/><rect x="3" y="7" width="3" height="3" fill="var(--blue)"/><rect x="7" y="11" width="3" height="3" fill="var(--blue)"/><circle cx="16" cy="4" r="3" fill="#fff"/></svg>Demolition</h4>
      <p>At Brovan Builders, our demolition services are designed to ensure the efficient and safe removal of structures while minimizing impact on the surrounding environment. We utilize advanced equipment and techniques to handle projects of any size, from residential buildings to large commercial sites. Our team of skilled professionals is trained to assess each project carefully, implementing effective strategies that prioritize safety and regulatory compliance. With a commitment to responsible waste management and recycling, Brovan Builders aims to deliver high-quality demolition services that pave the way for new development opportunities.</p>
    </article>

    <article class="service svc-grading">
      <h4><svg viewBox="0 0 20 18"><rect x="1" y="7" width="10" height="6" fill="#fff"/><rect x="3" y="3" width="5" height="4" fill="#fff"/><path d="M11 9 L17 5 L19 12 H13 Z" fill="#fff"/><circle cx="4" cy="15" r="2" fill="#fff"/><circle cx="9" cy="15" r="2" fill="#fff"/></svg>Grading</h4>
      <p>Brovan Builders specializes in comprehensive site grading and mass excavation and hauling services, ensuring that each project lays a solid foundation for future development. Our skilled team utilizes state-of-the-art equipment to effectively manage soil removal, leveling, and site preparation, significantly enhancing the efficiency of construction timelines. We prioritize precision and safety throughout the process, adhering to industry standards while minimizing environmental impact. Whether it's for residential, commercial, or industrial projects, our dedication to quality and attention to detail make us a reliable partner in achieving your site development goal.</p>
    </article>

    <article class="service svc-concrete">
      <h4><svg viewBox="0 0 20 18"><g fill="#fff"><rect x="1" y="1" width="8" height="4"/><rect x="11" y="1" width="8" height="4"/><rect x="1" y="7" width="4" height="4"/><rect x="7" y="7" width="8" height="4"/><rect x="17" y="7" width="2" height="4"/><rect x="1" y="13" width="8" height="4"/><rect x="11" y="13" width="8" height="4"/></g></svg>Structural Concrete</h4>
      <p>Our structural concrete and foundation division offers comprehensive solutions tailored to meet the diverse needs of our clients. We specialize in everything from slab-on-grade foundations to shoring and retaining walls, as well as hillside basements. Our dedicated team employs advanced techniques and high-quality materials to ensure stability, durability, and safety for all types of projects. With a commitment to excellence, we aim to deliver robust foundation systems that serve as the backbone for any construction endeavor.</p>
    </article>

    <svg class="photo" style="left:368px;top:32px" width="170" height="600" viewBox="0 0 170 600">
      <polygon points="0,8 45,0 0,28" fill="var(--ink)"/>
      <polygon points="0,10 170,0 170,205 0,205" fill="#9aa98a" role="img" aria-label="Photo: excavator clearing a hillside lot"/>
      <polygon points="0,215 170,195 170,408 0,418" fill="#b8a482" role="img" aria-label="Photo: graded pad below tall concrete retaining walls"/>
      <polygon points="0,428 170,418 170,600 0,600" fill="#a9a9a6" role="img" aria-label="Photo: concrete foundation walls on a hillside residential site"/>
      <polygon points="0,600 0,560 50,600" fill="var(--ink)"/>
      <polygon points="170,405 170,430 120,430" fill="var(--ink)"/>
    </svg>

    <div class="page-num">01</div>
    <div class="footer-url"><span class="slash"></span><span class="slash"></span><span class="bar">www.brovanbuildersinc.example</span></div>
  </section>

  <section class="page about">
    <svg class="bg" width="570" height="700" viewBox="0 0 570 700">
      <polygon points="0,0 240,0 0,250" fill="var(--blue)"/>
      <polygon points="0,262 0,305 570,305 570,272 110,272" fill="var(--grey-light)"/>
      <path d="M265 0 H570 V232 Q570 260 542 260 H20 Z" fill="#2a2a2c"/>
      <polygon points="265,0 290,0 45,260 20,260" fill="#3b3b3e"/>
      <polygon points="415,350 552,336 552,610 455,626 415,600" fill="#b29a74" role="img" aria-label="Photo: compact excavator on a graded lot overlooking the city"/>
      <polygon points="395,336 450,336 395,378" fill="var(--ink)"/>
      <polygon points="552,560 552,630 478,630" fill="var(--blue)"/>
    </svg>
    <h2 class="layer intro-title">BROVAN BUILDERS</h2>
    <p class="layer intro"><b>Brovan Builders</b> is a premier Los Angeles-based contractor specializing in demolition, grading, and structural concrete services, with a strong emphasis on hillside residential construction. Our expertise is rooted in a deep understanding of the unique challenges presented by hillside properties, allowing us to deliver safe, efficient, and innovative solutions that meet the highest industry standards. Committed to excellence, we leverage cutting-edge technology and skilled craftsmanship to ensure the structural integrity and aesthetic appeal of every project we undertake. Our dedication to quality and customer satisfaction has established Brovan Builders as a trusted partner in the dynamic landscape of residential construction in Southern California.</p>
    <h2 class="layer section-title who">WHO WE ARE</h2>
    <div class="layer who-text">
      <p><b>Brovan Builders</b> is a leading construction firm established in 2019, driven by a commitment to excellence and innovation in the building industry. With a team of seasoned professionals, we specialize in delivering high-quality residential and commercial projects tailored to meet our clients' specific needs.</p>
      <p>Our mission centers on building lasting relationships with our clients, ensuring open communication and collaboration throughout each phase of the construction process. We prioritize safety, sustainability, and efficiency, employing the latest industry practices and technologies to enhance project outcomes.</p>
      <p>At Brovan Builders, we take pride in our ability to transform visions into reality, providing not just structures but spaces that inspire and endure. Our diverse portfolio showcases our versatility and dedication to quality craftsmanship, making us a trusted partner in the construction landscape.</p>
    </div>
    <div class="footer-url"><span class="bar">www.brovanbuildersinc.example</span><span class="slash"></span><span class="slash"></span></div>
    <div class="page-num">02</div>
  </section>
</div>

</body>
</html>
```